business card deign

Logo needs the following on it.
1. attached logo
2. Tagline - "Cold drinks, loud music, long nights...we bring it all!"
3. Name- Dalton Pikes, Founder and CPO
4. Address - 412 E. Carver Avenue, Ste 2207, Tampa, FL. 33917
5. Phone - 555.318.4726

```html
<!DOCTYPE html>
<html lang="en">
<head>
<meta charset="utf-8">
<title>Frostline Business Card</title>
<link href="https://fonts.googleapis.com/css2?family=Roboto+Condensed:wght@400;700&family=Roboto:wght@400&display=swap" rel="stylesheet">
<style>
  :root {
    --backdrop: #d3d4d6;
    --card: #121212;
    --ink: #ffffff;
    --ink-soft: #e9e9e9;
  }
  * { margin: 0; padding: 0; box-sizing: border-box; }
  html, body {
    width: 900px;
    height: 1200px;
    overflow: hidden;
    background: var(--backdrop);
  }
  .sheet {
    position: relative;
    width: 900px;
    height: 1200px;
  }
  .card {
    position: absolute;
    left: 135px;
    width: 630px;
    height: 357px;
    background: var(--card);
    color: var(--ink);
  }
  .card--front { top: 214px; }
  .card--back { top: 628px; height: 358px; }

  .wordmark {
    font-family: "Roboto Condensed", "Arial Narrow", sans-serif;
    font-weight: 700;
    color: var(--ink);
    white-space: nowrap;
    line-height: 1;
    text-align: center;
  }
  .card--front .wordmark {
    position: absolute;
    left: 0;
    right: 0;
    top: 144px;
    font-size: 68px;
  }
  .card--back .wordmark {
    position: absolute;
    left: 40px;
    width: 250px;
    top: 160px;
    font-size: 38px;
  }
  .divider {
    position: absolute;
    left: 314px;
    top: 97px;
    width: 2px;
    height: 164px;
    background: var(--ink);
  }
  .contact {
    position: absolute;
    left: 343px;
    top: 102px;
    font-family: "Roboto", Arial, sans-serif;
    color: var(--ink-soft);
  }
  .contact__name {
    font-family: "Roboto Condensed", "Arial Narrow", sans-serif;
    font-weight: 700;
    font-size: 29px;
    line-height: 1;
    color: var(--ink);
    letter-spacing: 0.01em;
  }
  .contact__role {
    margin-top: 8px;
    font-size: 14px;
    letter-spacing: 0.03em;
  }
  .contact__phone {
    margin-top: 26px;
    display: flex;
    align-items: center;
    gap: 7px;
    font-size: 17px;
    letter-spacing: 0.06em;
  }
  .contact__phone svg { width: 11px; height: 11px; fill: var(--ink); }
  .contact__address {
    margin-top: 12px;
    font-size: 14.5px;
    line-height: 26px;
    letter-spacing: 0.02em;
  }
  .tagline {
    position: absolute;
    left: 0;
    right: 0;
    top: 302px;
    text-align: center;
    font-family: "Roboto Condensed", "Arial Narrow", sans-serif;
    font-weight: 700;
    font-size: 16px;
    letter-spacing: 0.05em;
    color: var(--ink);
  }
</style>
</head>
<body>
<main class="sheet">
  <section class="card card--front" aria-label="Card front">
    <div class="wordmark">Frostline</div>
  </section>

  <section class="card card--back" aria-label="Card back">
    <div class="wordmark">Frostline</div>
    <div class="divider"></div>
    <div class="contact">
      <div class="contact__name">DALTON PIKES</div>
      <div class="contact__role">Founder and CPO</div>
      <div class="contact__phone">
        <svg viewBox="0 0 24 24" aria-hidden="true"><path d="M6.6 10.8a15.1 15.1 0 0 0 6.6 6.6l2.2-2.2c.3-.3.7-.4 1-.2 1.1.4 2.3.6 3.6.6.6 0 1 .4 1 1V20c0 .6-.4 1-1 1C10.6 21 3 13.4 3 4c0-.6.4-1 1-1h3.5c.6 0 1 .4 1 1 0 1.3.2 2.5.6 3.6.1.3 0 .7-.2 1z"/></svg>
        <span>555.318.4726</span>
      </div>
      <div class="contact__address">
        412 E. Carver Avenue, Ste 2207<br>
        Tampa, FL. 33917
      </div>
    </div>
    <p class="tagline">Cold drinks, loud music, long nights...we bring it all!</p>
  </section>
</main>
</body>
</html>
```